Business Card Design

I need a business card design for my new business based on Long Island, NY also serving NYC called Pawhaven Retreat. I have built a website with cardmint that can be looked at as a basis for the card. It is pawhavenretreat.com.

I board Labrador Retrievers in my home. Specialize in one breed. Cage free environment. Dogs have full run of home and fenced in property. Pawhaven Retreat is a one-of-a-kind, high-quality dog-boarding provider serving specifically Labrador Retrievers. By working with a dog I am comfortable with, I am able to offer the best care for all pets that come through my door. I work with Lab owners in the Long Island/NYC area to provide an
in-home safe, reliable and fun environment for daycare and overnight stays.

I provide a unique boarding experience for Labrador Retrievers on Long Island. Your Lab should be well mannered, housebroken and good with other dogs. Provided your pet is well mannered and house trained, my boarding services allow dogs to experience a cage-free stay while having free roam of my home and property. This allows owners a unique alternative to a kennel, giving pets the chance to experience a home away from home rather than chain linked fences and cold concrete floors.
As a guest at Pawhaven Retreat, your dog will get:

4-star kibble
Access to my in-ground pool
All-natural snack selection
Companionship of other retrievers including my two
Full run of entire home and fenced-in backyard
Photos AND videos posted to Snapgram so you can see your dog having fun while away
Toys, bones and affection

I think it is important to have a pic of the 3 colored labs below. Also the picture of my own personal labs ..the white one with the black puppy. Maybe some paw prints. If using any imagery that MUST look EXACTLY like labrador retriever no generic dogs. Thank you
Updates

The Back of the Card should have the following: The background should be one of the pictures I sent (white dog in pool or another pic I included) At Pawhaven Retreat your Lab gets: Cage Free Environment Full run of my home and fenced in yard In-ground pool Toys and affection Companionship of other Labrador Retrievers Photos and Videos posted Snapgram of your loved one FRONT OF THE CARD: should include picture of the 3 labs (yellow white brown) OR picture of white dog in pool. Pawhaven Retreat should be in larger font than the rest. the following can be in any order. Tom Pelley Commack, NY in Central Long Island pawhavenretreat.com 631-555-0192

Industry/Entity Type

Environment

Contact Information for Business Card

Pawhaven Retreat
Commack, NY
Tom Pelley
hello@pawhavenretreat.com
631-555-0192

```html
<!DOCTYPE html>
<html lang="en">
<head>
<meta charset="utf-8">
<title>Pawhaven Retreat – Business Card</title>
<link rel="stylesheet" href="https://fonts.googleapis.com/css2?family=Inter:wght@300;400&display=swap">
<style>
  :root {
    --ink: #111111;
    --paper: #ffffff;
    --band: #000000;
    --accent: #f2ea1a;
    --backdrop: #e9e6e1;
    --photo-warm: #c98a3a;
    --photo-cream: #ece8df;
    --photo-dark: #2b2624;
  }
  * { box-sizing: border-box; margin: 0; padding: 0; }
  html, body {
    width: 1200px; height: 848px; overflow: hidden;
    background: var(--backdrop);
    font-family: "Inter", "Helvetica Neue", Arial, sans-serif;
    color: var(--ink);
  }
  .sheet {
    width: 1200px; height: 848px;
    display: flex; flex-direction: column; align-items: center; justify-content: center;
    gap: 36px;
  }
  .card {
    position: relative;
    width: 640px; height: 366px;
    overflow: hidden;
    box-shadow: 0 6px 18px rgba(0,0,0,0.18);
  }

  /* Front */
  .card--front { background: var(--paper); }
  .front__name {
    position: absolute; left: 54px; top: 66px;
    font-size: 23px; font-weight: 300; letter-spacing: 0.2px;
  }
  .front__contacts {
    position: absolute; left: 108px; top: 196px;
    list-style: none; font-size: 16px; font-weight: 300; line-height: 27px;
  }
  .front__contacts li { display: flex; align-items: center; gap: 12px; }
  .front__contacts svg { width: 15px; height: 15px; flex: none; }
  .front__band {
    position: absolute; left: 0; bottom: 0; width: 100%; height: 104px;
    background: var(--band);
  }
  .front__brand {
    position: absolute; left: 82px; bottom: 28px;
    color: var(--accent); font-size: 36px; font-weight: 300; letter-spacing: -0.3px;
  }
  .front__photo {
    position: absolute; left: 326px; top: -172px;
    width: 450px; height: 450px; border-radius: 50%;
    background:
      radial-gradient(circle at 48% 62%, var(--photo-cream) 0 22%, transparent 40%),
      radial-gradient(circle at 60% 80%, var(--photo-dark) 0 12%, transparent 26%),
      linear-gradient(135deg, #7a5a36 0%, var(--photo-warm) 35%, #8e7e74 70%, #b9b3ab 100%);
  }

  /* Back */
  .card--back { background: var(--band); }
  .back__arc {
    position: absolute; left: -470px; top: -140px;
    width: 1240px; height: 1240px; border-radius: 50%;
    background: var(--paper);
  }
  .back__content {
    position: absolute; left: 56px; top: 58px; width: 520px;
  }
  .back__lead { font-size: 20px; font-weight: 300; margin-bottom: 16px; }
  .perks { list-style: none; font-size: 15.5px; font-weight: 300; line-height: 24px; }
  .perks li { position: relative; padding-left: 30px; }
  .perks li::before {
    content: ""; position: absolute; left: 4px; top: 10px;
    width: 8px; height: 8px;
    border-left: 2.5px solid var(--ink); border-top: 2.5px solid var(--ink);
    transform: rotate(45deg);
  }
  .perks .perk--spaced { margin-top: 20px; }
</style>
</head>
<body>
<main class="sheet">

  <section class="card card--front" aria-label="Card front">
    <div class="front__photo" role="img" aria-label="Photo of a white Labrador lying beside a black Labrador puppy on a rug"></div>
    <p class="front__name">NY Tom Pelley</p>
    <ul class="front__contacts">
      <li>
        <svg viewBox="0 0 24 24" aria-hidden="true"><path fill="#111" d="M6.6 10.8a15.2 15.2 0 0 0 6.6 6.6l2.2-2.2a1 1 0 0 1 1-.25 11.4 11.4 0 0 0 3.6.57 1 1 0 0 1 1 1V20a1 1 0 0 1-1 1A17 17 0 0 1 3 4a1 1 0 0 1 1-1h3.5a1 1 0 0 1 1 1c0 1.25.2 2.45.57 3.6a1 1 0 0 1-.25 1z"/></svg>
        631-555-0192
      </li>
      <li>
        <svg viewBox="0 0 24 24" aria-hidden="true"><rect x="2" y="5" width="20" height="14" fill="none" stroke="#111" stroke-width="2"/><path d="M2 5l10 8 10-8M2 19l7-7M22 19l-7-7" fill="none" stroke="#111" stroke-width="2"/></svg>
        hello@pawhavenretreat.com
      </li>
    </ul>
    <div class="front__band"></div>
    <p class="front__brand">Pawhaven Retreat Commack</p>
  </section>

  <section class="card card--back" aria-label="Card back">
    <div class="back__arc"></div>
    <div class="back__content">
      <p class="back__lead">As a guest at Pawhaven Retreat, your dog will get</p>
      <ul class="perks">
        <li>4-star kibble</li>
        <li>Access to my in-ground pool</li>
        <li>All-natural snack selection</li>
        <li>Companionship of other retrievers including my two</li>
        <li>Full run of entire home and fenced-in backyard</li>
        <li>Photos AND videos posted to Snapgram so you can see<br>your dog having fun while away</li>
        <li class="perk--spaced">Toys, bones and affection</li>
      </ul>
    </div>
  </section>

</main>
</body>
</html>
```